High Tech Real Estate Startup needs a business card

We are developing an innovative real estate marketing product based around advanced search and virtual reality.

We talk to people, we need business cards.

Target Market(s)

The target market is technology professionals and realtors.

Contact Information for Business Card

The information to be included will include

Name
Title
Phone Number
E-mail Address
www.zelquin.com

It should use simple iconography for each one of those fields.

Font styles to use
Other font styles liked:
• Co, Jubilat, Avenir

Colors

Designer to choose colors to be used in the design.

Requirements
Must have
• Clean aesthetic,
• Good use of negative space.
• It should use our company logo, shown in the attached file. It is able to use the negative of that logo (coloured font and white background) and I have attached other acceptable accent colours in a swatch file.
Should not have
• Should not be too busy
• No extraneous text (slogans, tag lines etc)

```html
<!DOCTYPE html>
<html lang="en">
<head>
<meta charset="utf-8">
<title>Zelquin Business Card</title>
<link href="https://fonts.googleapis.com/css2?family=Montserrat:wght@400;500;600&display=swap" rel="stylesheet">
<style>
  :root {
    --backdrop: #4b4b4d;
    --paper: #fbfbfa;
    --teal: #14b9bc;
    --ink: #555759;
    --rule: #9a9a9a;
    --white: #ffffff;
  }
  * { box-sizing: border-box; margin: 0; padding: 0; }
  html, body {
    width: 1200px; height: 1134px; overflow: hidden;
    background: var(--backdrop);
    font-family: "Montserrat", Arial, sans-serif;
  }
  .canvas { position: relative; width: 1200px; height: 1134px; }
  .card {
    position: absolute; left: 261px; width: 675px; height: 381px;
    box-shadow: 0 3px 8px rgba(0,0,0,0.35);
  }
  .card-front { top: 161px; background: var(--paper); }
  .card-back { top: 589px; background: var(--teal); }

  .brand {
    position: absolute; top: 258px; left: 0; width: 100%;
    display: flex; justify-content: center; align-items: center; gap: 14px;
  }
  .brand-front { top: 64px; }
  .brand-mark { width: 44px; height: 44px; background: var(--teal); }
  .brand-name { font-weight: 600; color: var(--teal); font-size: 40px; letter-spacing: 1px; }

  .person {
    position: absolute; right: 341px; top: 284px; text-align: right;
  }
  .person-name { font-weight: 500; color: var(--teal); font-size: 29px; line-height: 1; }
  .person-title { color: var(--ink); font-size: 19px; margin-top: 6px; line-height: 1; }

  .divider {
    position: absolute; left: 339px; top: 264px; width: 1px; height: 70px;
    background: var(--rule);
  }
  .contacts { position: absolute; left: 373px; top: 271px; list-style: none; }
  .contacts li {
    display: flex; align-items: center; gap: 9px;
    height: 27px; color: var(--ink); font-size: 16.5px;
  }
  .contacts svg { width: 17px; height: 17px; fill: var(--teal); flex: none; }

  .back-name {
    position: absolute; left: 0; width: 100%; top: 150px; text-align: center;
    color: var(--white); font-weight: 600; font-size: 80px; line-height: 1; letter-spacing: 2px;
  }
</style>
</head>
<body>
<div class="canvas">
  <section class="card card-front">
    <div class="brand brand-front">
      <span class="brand-mark"></span>
      <span class="brand-name">ZELQUIN</span>
    </div>
    <div class="person">
      <p class="person-name">Dana Whitlock</p>
      <p class="person-title">President</p>
    </div>
    <div class="divider"></div>
    <ul class="contacts">
      <li>
        <svg viewBox="0 0 24 24" aria-hidden="true"><path d="M6.6 10.8c1.4 2.8 3.8 5.1 6.6 6.6l2.2-2.2c.3-.3.7-.4 1-.2 1.1.4 2.3.6 3.6.6.6 0 1 .4 1 1V20c0 .6-.4 1-1 1C10.6 21 3 13.4 3 4c0-.6.4-1 1-1h3.5c.6 0 1 .4 1 1 0 1.3.2 2.5.6 3.6.1.3 0 .7-.2 1l-2.3 2.2z"/></svg>
        <span>555 204 7183</span>
      </li>
      <li>
        <svg viewBox="0 0 24 24" aria-hidden="true"><path d="M2 5h20v14H2z M2 5l10 7 10-7" /><path d="M3 6.5l9 6.3 9-6.3V18H3z" fill="var(--teal)"/><path d="M2 5h20l-10 7z" fill="var(--teal)"/></svg>
        <span>info@zelquin.com</span>
      </li>
      <li>
        <svg viewBox="0 0 24 24" aria-hidden="true"><circle cx="12" cy="12" r="10"/><path d="M2 12h20M12 2c3 3 3 17 0 20M12 2c-3 3-3 17 0 20M4 7h16M4 17h16" stroke="var(--paper)" stroke-width="1.3" fill="none"/></svg>
        <span>www.zelquin.com</span>
      </li>
    </ul>
  </section>

  <section class="card card-back">
    <p class="back-name">ZELQUIN</p>
  </section>
</div>
</body>
</html>
```